Banner to be displayed at local Farmers Market Booth.

Graphic Design Brief: Farmers Market Banner Contest

Project Overview:We are seeking talented graphic designers to create a visually appealing banner for our booth at the local farmers market. Our company specializes in healthy, all-natural dog and cat treats, and we want a banner that captures our brand identity while drawing in pet owners who value quality and nutrition for their furry friends.

Banner Specifications:

Size: 24 inches x 60 inches (Horizontal orientation) 24" High X 60 wide

Theme: Vintage/Retro

Style: Warm, inviting, nostalgic with a touch of rustic charm

Colors: Earthy, muted tones such as warm browns, soft greens, and creamy yellows. Pops of red or blue may be used sparingly for accents. OR Black and White with gray scales. Would like to see both

Typography: Retro-style fonts that are readable and align with the vintage aesthetic.

Key Elements to Include: website (www.moltbyfarms.com)

Company Name: Moltby Farms

Tagline: " Simply Honest Bites "
Imagery: Illustrations or stylized graphics of happy dogs and cats, possibly interacting with treats.

Emphasis on Natural Ingredients: Icons or design elements that subtly suggest freshness and quality (e.g., leaves, wheat, bones, or paw prints).

Farmers Market Appeal: A design that blends well with the artisanal, handmade, and farm-fresh atmosphere of the market.

Design Considerations:

The banner should be easily readable from a distance.

A balanced composition that doesn't feel overcrowded.

Should evoke trust and warmth while maintaining a professional look.

Avoid overly modern or sleek elements that don’t align with the vintage aesthetic.

Submission Requirements:

High-resolution digital file in PDF or AI format.

CMYK color mode for printing purposes.

Must include a mockup or preview of how it would look in a real farmers market setting.

We look forward to seeing your creative interpretations of our brand! If you have any questions, feel free to reach out.

Font styles to use
Other font styles liked:
• See attachement

Requirements
Nice to have
• Retro/Vintage,playful BUT NOT whimsical

```html
<!DOCTYPE html>
<html lang="en">
<head>
<meta charset="UTF-8">
<title>Moltby Farms – Market Banner</title>
<link href="https://fonts.googleapis.com/css2?family=Alfa+Slab+One&family=Fraunces:opsz,wght@72,900&display=swap" rel="stylesheet">
<style>
  :root {
    --backdrop: #e6e6e6;
    --cream: #ebe4d6;
    --cream-light: #f3eee4;
    --cream-shade: #d8cdb9;
    --rust-edge: #7a2a18;
    --ink: #1d1d1d;
    --band-red: #b5221f;
    --band-red-dark: #8f1815;
    --band-text: #e9dfcd;
    --coat-gold: #c99a55;
    --coat-deep: #8a6434;
    --coat-light: #e2c28c;
  }
  * { margin: 0; padding: 0; box-sizing: border-box; }
  html, body {
    width: 1200px;
    height: 581px;
    overflow: hidden;
    background: var(--backdrop);
  }
  .banner {
    position: absolute;
    left: 88px;
    top: 80px;
    width: 1024px;
    height: 408px;
    overflow: hidden;
    background:
      radial-gradient(ellipse at 35% 40%, var(--cream-light) 0%, var(--cream) 45%, var(--cream-shade) 100%);
    box-shadow:
      0 6px 14px rgba(0,0,0,0.35),
      inset 0 0 0 3px var(--rust-edge),
      inset 0 0 22px 6px rgba(122,42,24,0.55);
  }
  .brand-mark {
    position: absolute;
    left: 230px;
    top: 52px;
    width: 200px;
    text-align: center;
    white-space: nowrap;
    font-family: "Alfa Slab One", serif;
    font-size: 18px;
    line-height: 24px;
    color: var(--ink);
    letter-spacing: 0.5px;
  }
  .headline {
    position: absolute;
    left: 60px;
    top: 104px;
    width: 540px;
    text-align: center;
    font-family: "Alfa Slab One", serif;
    font-weight: 400;
    font-size: 62px;
    line-height: 70px;
    color: var(--ink);
    text-transform: uppercase;
    white-space: nowrap;
    text-shadow: 2px 3px 0 rgba(200,150,150,0.45);
  }
  .headline span { display: block; }
  .site-band {
    position: absolute;
    left: 0;
    bottom: 0;
    width: 100%;
    height: 80px;
    background: linear-gradient(180deg, var(--band-red) 0%, var(--band-red-dark) 100%);
    box-shadow: inset 0 0 16px rgba(60,10,5,0.55);
  }
  .site-address {
    position: absolute;
    left: 100px;
    top: 8px;
    white-space: nowrap;
    font-family: "Fraunces", serif;
    font-weight: 900;
    font-size: 48px;
    line-height: 60px;
    color: var(--band-text);
    letter-spacing: 0.5px;
  }
  .pet-portrait {
    position: absolute;
    left: 620px;
    top: 68px;
    width: 400px;
    height: 340px;
    border-radius: 190px 170px 0 0;
    background: radial-gradient(ellipse at 60% 35%, var(--coat-light) 0%, var(--coat-gold) 45%, var(--coat-deep) 100%);
  }
</style>
</head>
<body>
  <div class="banner">
    <div class="brand-mark">Moltby Farms</div>
    <h1 class="headline"><span>Simply</span><span>Honest</span><span>Bites</span></h1>
    <div class="site-band">
      <p class="site-address">moltbyfarms.com</p>
    </div>
    <div class="pet-portrait" role="img" aria-label="Illustration of a golden retriever hugging a calico cat"></div>
  </div>
</body>
</html>
```